Banner to be displayed at local Farmers Market Booth.

Graphic Design Brief: Farmers Market Banner Contest

Project Overview:We are seeking talented graphic designers to create a visually appealing banner for our booth at the local farmers market. Our company specializes in healthy, all-natural dog and cat treats, and we want a banner that captures our brand identity while drawing in pet owners who value quality and nutrition for their furry friends.

Banner Specifications:

Size: 24 inches x 60 inches (Horizontal orientation) 24" High X 60 wide

Theme: Vintage/Retro

Style: Warm, inviting, nostalgic with a touch of rustic charm

Colors: Earthy, muted tones such as warm browns, soft greens, and creamy yellows. Pops of red or blue may be used sparingly for accents. OR Black and White with gray scales. Would like to see both

Typography: Retro-style fonts that are readable and align with the vintage aesthetic.

Key Elements to Include: website (www.moltbyfarms.com)

Company Name: Moltby Farms

Tagline: " Simply Honest Bites "
Imagery: Illustrations or stylized graphics of happy dogs and cats, possibly interacting with treats.

Emphasis on Natural Ingredients: Icons or design elements that subtly suggest freshness and quality (e.g., leaves, wheat, bones, or paw prints).

Farmers Market Appeal: A design that blends well with the artisanal, handmade, and farm-fresh atmosphere of the market.

Design Considerations:

The banner should be easily readable from a distance.

A balanced composition that doesn't feel overcrowded.

Should evoke trust and warmth while maintaining a professional look.

Avoid overly modern or sleek elements that don’t align with the vintage aesthetic.

Submission Requirements:

High-resolution digital file in PDF or AI format.

CMYK color mode for printing purposes.

Must include a mockup or preview of how it would look in a real farmers market setting.

We look forward to seeing your creative interpretations of our brand! If you have any questions, feel free to reach out.

Font styles to use
Other font styles liked:
• See attachement

Requirements
Nice to have
• Retro/Vintage,playful BUT NOT whimsical

```html
<!DOCTYPE html>
<html lang="en">
<head>
<meta charset="utf-8">
<title>Moltby Farms — Market Banner</title>
<link rel="stylesheet" href="https://fonts.googleapis.com/css2?family=Oswald:wght@700&family=Yellowtail&family=Lilita+One&display=swap">
<style>
  :root {
    --page: #f4f4f2;
    --metal: #8d8d8d;
    --metal-dark: #5c5c5c;
    --panel: #111111;
    --panel-grain: #2a2a2a;
    --frame-line: #ffffff;
    --headline: #ffffff;
    --gold: #d39a22;
    --gold-deep: #7a4c0c;
    --pill: #c6c6c6;
    --ink: #161616;
    --art-light: #d8d8d8;
    --art-dark: #4a4a4a;
  }
  * { box-sizing: border-box; margin: 0; padding: 0; }
  html, body { width: 900px; height: 1200px; overflow: hidden; background: var(--page); }
  .canvas { position: relative; width: 900px; height: 1200px; }

  .banner {
    position: absolute; left: 40px; top: 436px; width: 820px; height: 328px;
    background: radial-gradient(circle at 30% 20%, #a6a6a6, var(--metal) 45%, var(--metal-dark));
    box-shadow: 0 18px 40px rgba(0,0,0,.35);
  }
  .banner__panel {
    position: absolute; inset: 14px;
    background:
      radial-gradient(ellipse at 55% 15%, #333 0%, transparent 45%),
      repeating-linear-gradient(0deg, var(--panel) 0 9px, var(--panel-grain) 9px 10px),
      var(--panel);
  }
  .banner__frame { position: absolute; inset: 0; width: 820px; height: 328px; }
  .banner__frame path { fill: none; stroke: var(--frame-line); stroke-width: 4; }
  .banner__frame circle { fill: #3a3a3a; }

  .brand-mark {
    position: absolute; left: 222px; top: 44px;
    display: flex; align-items: center; gap: 6px;
    font-family: "Oswald", sans-serif; font-weight: 700;
    font-size: 17px; letter-spacing: .5px; color: var(--headline);
  }
  .brand-mark__dot { width: 10px; height: 10px; border-radius: 50%; background: var(--headline); }

  .headline {
    position: absolute; left: 50px; top: 80px; width: 440px;
    font-family: "Oswald", sans-serif; font-weight: 700;
    font-size: 70px; line-height: 1; letter-spacing: -.5px;
    color: var(--headline); white-space: nowrap; text-align: center;
    transform: scaleY(1.3); transform-origin: top center;
    text-shadow: 2px 1px 0 var(--gold), 4px 2px 0 var(--gold), 6px 3px 0 var(--gold-deep);
  }
  .tagline {
    position: absolute; left: 165px; top: 168px; width: 210px;
    font-family: "Yellowtail", cursive; font-size: 86px; line-height: 1;
    color: var(--headline); text-align: center;
    transform: rotate(-5deg);
    text-shadow: 3px 2px 0 var(--gold), 5px 4px 0 var(--gold-deep);
  }

  .web-pill {
    position: absolute; left: 58px; top: 266px; width: 426px; height: 46px;
    background: var(--pill); border: 3px solid var(--frame-line);
    outline: 2px solid var(--ink); outline-offset: -6px;
    border-radius: 18px;
    display: flex; align-items: center; justify-content: center;
    font-family: "Lilita One", sans-serif; font-size: 34px; color: var(--ink);
    letter-spacing: .5px;
  }

  .pet-art {
    position: absolute; left: 498px; top: 40px; width: 306px; height: 280px;
    border-radius: 46% 46% 8px 8px / 40% 40% 8px 8px;
    background: radial-gradient(ellipse at 60% 35%, var(--art-light), #9a9a9a 55%, var(--art-dark));
  }
</style>
</head>
<body>
<main class="canvas">
  <section class="banner" aria-label="Moltby Farms market banner">
    <div class="banner__panel"></div>
    <svg class="banner__frame" viewBox="0 0 820 328" aria-hidden="true">
      <path d="M42 22 H778 A22 22 0 0 0 800 44 V284 A22 22 0 0 0 778 306 H42 A22 22 0 0 0 20 284 V44 A22 22 0 0 0 42 22 Z"/>
      <circle cx="8" cy="8" r="4"/><circle cx="812" cy="8" r="4"/>
      <circle cx="8" cy="320" r="4"/><circle cx="812" cy="320" r="4"/>
    </svg>

    <div class="brand-mark"><span class="brand-mark__dot"></span>Moltby Farms</div>
    <h1 class="headline">SIMPLY HONEST</h1>
    <p class="tagline">Bites</p>
    <div class="web-pill">moltbyfarms.com</div>
    <div class="pet-art" role="img" aria-label="Black and white engraved illustration of a golden retriever hugging a tabby cat"></div>
  </section>
</main>
</body>
</html>
```